UX Design for Analytics Web Application

http://velqoranthe.com/
We are tech & consulting company with analytics products (web applications), located at Rio de Janeiro, Brazil.

We are searching a partner do develop UX for our products, i.e, aesthetics, usability, HTML/CSS.

Currently we have a product suite and the goal is to make a pilot re-design project with one of our products.

The product of interest is interactive webapp that aims at data analysis, significantly different from blogs, e-commerce or landing pages.

We do have a software development team but we lack an UX & HTML expert. Currently we use Bootstrap templates but the results are insatisfatory.

So, the project scope is, to develop the arts (UX, aesthetics, etc) along with the code/mockup (HTML/CSS) for one of our product (3 pages).

This is a pilot project and there's potential to rehire for our other products. Code quality is of importance.

More details and specification can be found in attached files.

Target Market(s)

Executives, managers & consultants

Industry/Entity Type

It Company

Coding

Coded - Design and coding required

Number of Pages Required

3 page

Font styles to use
Sans Serif

Requirements
Must have
• (see attached files, prefer the pptx version))
• -Responsive
Nice to have
• (see attached files, prefer the pptx version)
Should not have
• -Avoid Green, Red and Yellow colors. They have a meaning of good, bad and average in our products.

```html
<!DOCTYPE html>
<html lang="en">
<head>
<meta charset="utf-8">
<title>Velqoranthe – Process Overview</title>
<link rel="stylesheet" href="https://fonts.googleapis.com/css2?family=Dosis:wght@400;500;600;700&family=Catamaran:wght@400;500&display=swap">
<style>
  :root{
    --dark:#444444;
    --panel:#3a3a3a;
    --white:#ffffff;
    --light:#f2f2f2;
    --card:#e1e1e1;
    --ink:#3c3c3c;
    --muted:#bdbdbd;
    --track:#d9d9d9;
    --accent:#3e9ad3;
    --navy:#2a5b8e;
    --violet:#7a5ea8;
    --steel:#6f86a3;
    --grey:#8c8c8c;
    --sky:#8cc4e8;
    --slider:#5a5a5a;
  }
  *{margin:0;padding:0;box-sizing:border-box}
  html,body{width:973px;height:1200px;overflow:hidden}
  body{position:relative;background:var(--light);font-family:"Dosis",sans-serif;color:var(--ink)}
  .overview{position:absolute;left:0;top:0;width:973px;height:639px;background:var(--dark);color:var(--white)}
  .menu-icon{position:absolute;left:30px;top:27px}
  .topbar{position:absolute;left:80px;top:0;width:813px;height:72px;background:var(--white)}
  .brand{position:absolute;left:12px;top:22px;display:flex;align-items:center;gap:8px;font-weight:600;font-size:26px;color:var(--ink)}
  .brand-dot{width:12px;height:12px;border-radius:50%;background:var(--ink)}
  .nav{position:absolute;right:34px;top:23px;display:flex;gap:20px;font-size:12px;color:var(--ink)}
  .nav-item{display:flex;align-items:center;gap:7px}
  .page-title{position:absolute;left:125px;top:104px;font-size:26px;font-weight:700;letter-spacing:1px}
  .stat{position:absolute;top:174px;width:180px;text-align:center}
  .stat-ring{width:114px;height:114px;margin:0 auto;border:2px solid var(--accent);border-radius:50%;display:flex;align-items:center;justify-content:center;font-size:40px;font-weight:500}
  .stat-label{margin-top:16px;font-size:13px;font-family:"Catamaran",sans-serif}
  .summary{position:absolute;left:471px;top:166px;width:403px;height:190px;background:var(--panel)}
  .summary-label{position:absolute;left:28px;font-size:17px}
  .slider{position:absolute;left:172px;top:44px;width:198px;height:5px;background:var(--slider)}
  .slider-fill{width:140px;height:5px;background:var(--accent)}
  .slider-knob{position:absolute;left:132px;top:-6px;width:17px;height:17px;border-radius:50%;background:var(--accent);border:2px solid var(--white)}
  .slider-value{position:absolute;left:303px;top:64px;font-size:8px;font-family:"Catamaran",sans-serif}
  .feed-text{position:absolute;left:127px;top:85px;width:250px;font-size:10px;line-height:17px;color:var(--muted);font-family:"Catamaran",sans-serif;text-align:justify}
  .feed-meta{position:absolute;left:127px;top:131px;display:flex;gap:16px;font-size:11px;color:var(--muted)}
  .feed-meta span{display:flex;align-items:center;gap:7px}
  .small{font-size:11px}
  .chart{position:absolute;left:0;top:360px}
  .chart text{font-family:"Catamaran",sans-serif;font-size:10px;fill:var(--white)}
  .card{position:absolute;width:267px;height:196px;background:var(--card)}
  .card-title{position:absolute;left:19px;top:18px;font-size:20px;font-weight:500;letter-spacing:.5px}
  .donut{position:absolute;left:20px;top:57px}
  .donut-value{position:absolute;left:20px;top:84px;width:112px;text-align:center}
  .donut-value strong{display:block;font-size:31px;font-weight:500;line-height:30px}
  .donut-value small{display:block;font-size:12px;margin-top:2px}
  .legend{position:absolute;left:152px;top:112px;list-style:none;font-size:13px}
  .legend li{display:flex;align-items:center;gap:8px;height:20.5px}
  .legend i{width:9px;height:9px}
  .arc{fill:none;stroke-width:4}
  .desc{position:absolute;width:250px;font-size:10.5px;line-height:17px;font-family:"Catamaran",sans-serif;color:var(--ink)}
  .add-card{display:flex;flex-direction:column;align-items:center;justify-content:center}
  .add-plus{width:38px;height:38px;position:relative;margin-top:-20px}
  .add-plus::before,.add-plus::after{content:"";position:absolute;background:#cfcfcf}
  .add-plus::before{left:15px;top:0;width:7px;height:38px}
  .add-plus::after{left:0;top:15px;width:38px;height:7px}
  .add-label{margin-top:26px;font-size:19px;letter-spacing:.8px;font-weight:500;color:#555}
  .footer{position:absolute;top:1177px;font-size:10px;font-family:"Catamaran",sans-serif}
</style>
</head>
<body>
<section class="overview">
  <svg class="menu-icon" width="18" height="14" viewBox="0 0 18 14"><rect y="0" width="18" height="2.4" fill="#9a9a9a"/><rect y="5.8" width="18" height="2.4" fill="#9a9a9a"/><rect y="11.6" width="18" height="2.4" fill="#9a9a9a"/></svg>

  <header class="topbar">
    <div class="brand"><span class="brand-dot"></span>Velqoranthe</div>
    <nav class="nav">
      <span class="nav-item"><svg width="14" height="14" viewBox="0 0 14 14"><circle cx="7" cy="7" r="6" fill="none" stroke="#3c3c3c"/><rect x="6.3" y="3.5" width="1.4" height="4.5" fill="#3c3c3c"/><rect x="6.3" y="9" width="1.4" height="1.4" fill="#3c3c3c"/></svg>Notification</span>
      <span class="nav-item"><svg width="12" height="14" viewBox="0 0 12 14"><circle cx="6" cy="4" r="3" fill="none" stroke="#3c3c3c"/><path d="M1 13v-2a5 4 0 0 1 10 0v2z" fill="none" stroke="#3c3c3c"/></svg>Profile</span>
      <span class="nav-item"><svg width="14" height="14" viewBox="0 0 14 14"><circle cx="7" cy="7" r="2.2" fill="none" stroke="#3c3c3c"/><circle cx="7" cy="7" r="5.5" fill="none" stroke="#3c3c3c" stroke-dasharray="2 1.5"/></svg>Configuration</span>
    </nav>
  </header>

  <h1 class="page-title">PROCESS OVERVIEW</h1>

  <div class="stat" style="left:109px"><div class="stat-ring">04</div><p class="stat-label">Active processes</p></div>
  <div class="stat" style="left:289px"><div class="stat-ring">03</div><p class="stat-label">Completed processes</p></div>

  <aside class="summary">
    <div class="summary-label" style="top:35px">Completions : 72%</div>
    <div class="slider"><div class="slider-fill"></div><div class="slider-knob"></div></div>
    <div class="slider-value">72%</div>
    <div class="summary-label" style="top:82px">Activity feed :</div>
    <p class="feed-text">Sed ut perspiciatis unde omnis iste natus error sit voluptatem accusantium ...</p>
    <div class="feed-meta">
      <span><svg width="10" height="12" viewBox="0 0 12 14"><circle cx="6" cy="4" r="3" fill="none" stroke="#bdbdbd"/><path d="M1 13v-2a5 4 0 0 1 10 0v2z" fill="none" stroke="#bdbdbd"/></svg>Tomas Brell</span>
      <span><svg width="11" height="11" viewBox="0 0 11 11"><rect x=".5" y="1.5" width="10" height="9" fill="none" stroke="#bdbdbd"/><path d="M.5 4h10M3 0v3M8 0v3M3 6h1M5 6h1M7 6h1M3 8h1M5 8h1M7 8h1" stroke="#bdbdbd"/></svg>12-03-2017</span>
    </div>
    <div class="summary-label" style="top:153px">Expences : <span class="small">Sum of Total : $190</span></div>
  </aside>

  <svg class="chart" width="973" height="270" viewBox="0 360 973 270">
    <text transform="rotate(-90 150 456)" x="150" y="456" text-anchor="middle">Expenses</text>
    <g text-anchor="end">
      <text x="193" y="378">$1500</text><text x="193" y="413">$1200</text><text x="193" y="449">$900</text>
      <text x="193" y="484">$600</text><text x="193" y="520">$300</text><text x="193" y="555">$100</text>
    </g>
    <rect x="227" y="509" width="24" height="73" fill="var(--violet)"/>
    <rect x="285" y="476" width="24" height="106" fill="var(--navy)"/>
    <rect x="345" y="436" width="24" height="146" fill="var(--sky)"/>
    <rect x="407" y="374" width="24" height="208" fill="var(--grey)"/>
    <rect x="468" y="476" width="24" height="106" fill="var(--accent)"/>
    <line x1="198" y1="370" x2="198" y2="602" stroke="#fff" stroke-width="1.2"/>
    <line x1="182" y1="582" x2="864" y2="582" stroke="#fff" stroke-width="1.2"/>
    <g text-anchor="middle">
      <text x="237" y="602">Process1</text><text x="298" y="602">Process2</text><text x="360" y="602">Process3</text>
      <text x="420" y="602">Process4</text><text x="482" y="602">Process5</text><text x="543" y="602">Process6</text>
      <text x="680" y="602" letter-spacing="2">......................</text>
      <text x="842" y="602">Processn</text>
      <text x="413" y="620">Process</text>
    </g>
  </svg>
</section>

<article class="card" style="left:80px;top:665px">
  <h2 class="card-title">PROCESS #1</h2>
  <svg class="donut" width="112" height="112" viewBox="0 0 112 112">
    <circle cx="56" cy="56" r="50" class="arc" stroke="var(--track)"/>
    <circle cx="56" cy="56" r="50" class="arc" stroke="var(--accent)" pathLength="360" stroke-dasharray="45 999" transform="rotate(90 56 56)"/>
    <circle cx="56" cy="56" r="50" class="arc" stroke="var(--navy)" pathLength="360" stroke-dasharray="95 999" transform="rotate(135 56 56)"/>
    <circle cx="56" cy="56" r="50" class="arc" stroke="var(--violet)" pathLength="360" stroke-dasharray="100 999" transform="rotate(230 56 56)"/>
  </svg>
  <div class="donut-value"><strong>45%</strong><small>$20 &lt; $300</small></div>
  <ul class="legend"><li><i style="background:var(--violet)"></i>Current Stage</li><li><i style="background:var(--navy)"></i>Expenses</li><li><i style="background:var(--accent)"></i>Completion 45%</li></ul>
</article>
<p class="desc" style="left:98px;top:876px">Sed ut perspiciatis unde omnis iste natus error sit voluptatem accusantium ...</p>

<article class="card" style="left:353px;top:665px">
  <h2 class="card-title" style="left:24px">PROCESS #2</h2>
  <svg class="donut" width="112" height="112" viewBox="0 0 112 112" style="left:24px">
    <circle cx="56" cy="56" r="50" class="arc" stroke="var(--track)"/>
    <circle cx="56" cy="56" r="50" class="arc" stroke="var(--accent)" pathLength="360" stroke-dasharray="75 999" transform="rotate(90 56 56)"/>
    <circle cx="56" cy="56" r="50" class="arc" stroke="var(--navy)" pathLength="360" stroke-dasharray="65 999" transform="rotate(165 56 56)"/>
    <circle cx="56" cy="56" r="50" class="arc" stroke="var(--violet)" pathLength="360" stroke-dasharray="88 999" transform="rotate(232 56 56)"/>
  </svg>
  <div class="donut-value" style="left:24px"><strong>55%</strong><small>$20 &lt; $300</small></div>
  <ul class="legend" style="left:150px"><li><i style="background:var(--violet)"></i>Current Stage</li><li><i style="background:var(--navy)"></i>Expenses</li><li><i style="background:var(--accent)"></i>Completion 55%</li></ul>
</article>
<p class="desc" style="left:373px;top:876px">Sed ut perspiciatis unde omnis iste natus error sit voluptatem accusantium ...</p>

<article class="card" style="left:625px;top:665px">
  <h2 class="card-title">PROCESS #3</h2>
  <svg class="donut" width="112" height="112" viewBox="0 0 112 112" style="left:26px">
    <circle cx="56" cy="56" r="50" class="arc" stroke="var(--track)"/>
    <circle cx="56" cy="56" r="50" class="arc" stroke="var(--accent)" pathLength="360" stroke-dasharray="75 999" transform="rotate(90 56 56)"/>
    <circle cx="56" cy="56" r="50" class="arc" stroke="var(--grey)" pathLength="360" stroke-dasharray="70 999" transform="rotate(165 56 56)"/>
    <circle cx="56" cy="56" r="50" class="arc" stroke="var(--violet)" pathLength="360" stroke-dasharray="80 999" transform="rotate(237 56 56)"/>
  </svg>
  <div class="donut-value" style="left:26px"><strong>35%</strong><small>$20 &lt; $300</small></div>
  <ul class="legend" style="left:146px"><li><i style="background:var(--violet)"></i>Current Stage</li><li><i style="background:var(--grey)"></i>Expenses</li><li><i style="background:var(--accent)"></i>Completion 35%</li></ul>
</article>
<p class="desc" style="left:643px;top:876px">Sed ut perspiciatis unde omnis iste natus error sit voluptatem accusantium ...</p>

<article class="card" style="left:80px;top:924px">
  <h2 class="card-title" style="left:25px">PROCESS #4</h2>
  <svg class="donut" width="112" height="112" viewBox="0 0 112 112" style="left:24px">
    <circle cx="56" cy="56" r="50" class="arc" stroke="var(--track)"/>
    <circle cx="56" cy="56" r="50" class="arc" stroke="var(--accent)" pathLength="360" stroke-dasharray="75 999" transform="rotate(90 56 56)"/>
    <circle cx="56" cy="56" r="50" class="arc" stroke="var(--navy)" pathLength="360" stroke-dasharray="65 999" transform="rotate(165 56 56)"/>
    <circle cx="56" cy="56" r="50" class="arc" stroke="var(--violet)" pathLength="360" stroke-dasharray="88 999" transform="rotate(232 56 56)"/>
  </svg>
  <div class="donut-value" style="left:24px;top:86px"><strong>55%</strong><small>$20 &lt; $300</small></div>
  <ul class="legend" style="left:152px;top:118px"><li><i style="background:var(--violet)"></i>Current Stage</li><li><i style="background:var(--navy)"></i>Expenses</li><li><i style="background:var(--accent)"></i>Completion 55%</li></ul>
</article>
<p class="desc" style="left:101px;top:1134px">Sed ut perspiciatis unde omnis iste natus error sit voluptatem accusantium ...</p>

<article class="card add-card" style="left:353px;top:924px">
  <div class="add-plus"></div>
  <div class="add-label">ADD NEW PROCESS</div>
</article>

<footer>
  <p class="footer" style="left:707px">Copyrights © 2017 - All Rights Reserved</p>
  <p class="footer" style="left:927px;top:1175px;font-size:9px">M1</p>
</footer>
</body>
</html>
```